New Mechanical Maintenance business needs website

New Mechanical Maintenance business in Perth Western Australia needs a nice and easy to navigate website. Showing what we do and how we can be the right fit for other small to medium size business by offering personalized service from our highly skilled team. We deal with both fixed plant repairs like food and chemical processing facilities to heavy equipment like drill rigs, Large boats and earthmoving equipment.

Target Market(s)

Small to medium business to offer personalized services/packages

Industry/Entity Type

e deal with both fixed plant repairs like food and chemical processing facilities to heavy equipment like drill rigs, Large boats and earthmoving equipment.

Coding

Coded - Design and coding required

Number of Pages Required

4 page

Font styles to use
Serif

Colors
0054AA
0677BA
7BADD7
CADEEF
E8F1F8

Requirements
Must have
• A website that is easy to navigate but covers off on the range of services/maintenance we can provide

```html
<!DOCTYPE html>
<html lang="en">
<head>
<meta charset="utf-8">
<title>KRV Maintenance</title>
<link href="https://fonts.googleapis.com/css2?family=Poppins:wght@400;500;600;700;800;900&display=swap" rel="stylesheet">
<style>
:root{
  --blue:#0054AA;
  --blue-mid:#0677BA;
  --blue-soft:#7BADD7;
  --ink:#111;
  --grey:#555;
  --muted:#999;
  --field:#f1f1f1;
  --black:#000;
  --white:#fff;
  --star:#f2a900;
}
*{margin:0;padding:0;box-sizing:border-box}
html,body{width:1200px;height:3903px;overflow:hidden}
body{position:relative;font-family:"Poppins",sans-serif;color:var(--ink);background:var(--white)}
.abs{position:absolute}
.center{left:0;width:1200px;text-align:center}

/* header */
.site-header{position:absolute;top:0;left:0;width:1200px;height:88px;background:var(--white);z-index:3}
.brand{position:absolute;left:106px;top:0;width:158px;height:148px;border-radius:0 0 79px 79px;background:var(--white);display:flex;flex-direction:column;align-items:center;justify-content:center;z-index:4}
.brand span{font-weight:600;color:#4a4f57;font-size:30px;letter-spacing:8px;line-height:1}
.brand small{font-weight:600;color:#4a4f57;font-size:11px;letter-spacing:2px;margin-top:6px}
.nav a{position:absolute;top:32px;font-size:16px;color:#222;text-decoration:none}
.login{position:absolute;left:956px;top:20px;width:124px;height:45px;background:var(--blue);color:var(--white);border-radius:4px 4px 14px 4px;font-weight:600;font-size:16px;display:flex;align-items:center;justify-content:center;gap:8px}

/* hero */
.hero{position:absolute;top:88px;left:0;width:1200px;height:671px;background:linear-gradient(180deg,#2b1a10 0%,#7a4416 28%,#c77a2a 42%,#0a0a0a 52%,#b96a22 66%,#4a2a12 85%,#1d120a 100%)}
.hero-welcome{top:212px;font-size:33px;font-weight:700;color:var(--white)}
.hero-big{top:238px;font-size:172px;font-weight:900;color:var(--white);line-height:1;letter-spacing:2px}
.hero-sub{top:412px;font-size:60px;font-weight:800;color:var(--white);line-height:1}
.hero-text{top:490px;font-size:16px;color:var(--white);line-height:30px}
.btn{position:absolute;display:flex;align-items:center;justify-content:center;font-weight:600;border-radius:4px 4px 16px 4px}
.btn-blue{background:var(--blue);color:var(--white)}

/* services */
.section-title{font-size:38px;font-weight:800;color:var(--ink)}
.services-text{position:absolute;left:160px;width:880px;top:906px;text-align:center;font-size:15px;line-height:26px;color:#222}
.service-card{position:absolute;width:243px;background:var(--white);padding:4px;box-shadow:0 6px 20px rgba(0,0,0,.12)}
.service-card .photo{width:100%;height:100%;border:5px solid var(--blue);position:relative}
.service-card .label{position:absolute;bottom:26px;left:0;width:100%;text-align:center;color:var(--white);font-weight:700;font-size:19px;line-height:26px}

/* about */
.about-band{position:absolute;left:386px;top:1571px;width:814px;height:502px;background:linear-gradient(90deg,#0a62b0,var(--blue-mid))}
.about-photo{position:absolute;left:38px;top:1558px;width:530px;height:530px;border-radius:50%;background:radial-gradient(circle at 55% 45%,#9b8a6e 0%,#5e5a52 45%,#2e2c2a 100%)}
.about-title{position:absolute;left:595px;top:1640px;font-size:34px;font-weight:700;color:var(--white)}
.about-text{position:absolute;left:598px;top:1705px;width:490px;font-size:14.5px;line-height:30px;color:var(--white)}
.btn-white{background:var(--white);color:var(--blue)}

/* testimonials */
.t-photo{position:absolute;top:2304px;width:300px;height:302px;background:linear-gradient(160deg,#e4e4e4,#b9a592 60%,#d9d9d9)}
.t-card{position:absolute;top:2507px;width:312px;height:228px;background:var(--white);box-shadow:0 8px 24px rgba(0,0,0,.08);padding:22px 23px}
.t-card h3{font-size:16px;font-weight:600;color:#111}
.t-card .role{font-size:12px;color:var(--muted);margin-top:2px}
.t-card .rule{width:42px;height:3px;background:var(--blue);margin:8px 0 8px}
.t-card .stars{color:var(--star);font-size:15px;letter-spacing:3px}
.t-card p{font-size:12.5px;line-height:23px;color:var(--muted);margin-top:6px}

/* contact */
.footer-bg{position:absolute;top:3294px;left:0;width:1200px;height:609px;background:var(--black)}
.contact-card{position:absolute;left:98px;top:2836px;width:1003px;height:546px;background:var(--white);border-radius:75px 0 75px 0;box-shadow:0 0 30px rgba(0,0,0,.06)}
.contact-text{position:absolute;left:200px;width:800px;top:2940px;text-align:center;font-size:15px;line-height:35px;color:#222}
.field{position:absolute;background:var(--field);border-radius:26px;font-size:13px;color:#777;padding:0 25px;display:flex;align-items:center;justify-content:space-between}
.field.area{align-items:flex-start;padding-top:15px}

/* footer */
.foot-brand{position:absolute;left:121px;top:3515px;width:280px;height:220px;display:flex;flex-direction:column;align-items:center;justify-content:center}
.foot-brand span{font-size:62px;font-weight:600;color:#4a4f57;letter-spacing:14px;line-height:1}
.foot-brand small{font-size:20px;font-weight:600;color:#4a4f57;letter-spacing:4px;margin-top:10px}
.foot-h{position:absolute;color:var(--white);font-weight:700}
.newsletter{position:absolute;left:515px;top:3565px;width:388px;height:36px;border:1px solid #666;border-radius:6px 0 6px 6px;display:flex;overflow:hidden}
.newsletter .input{flex:1;font-size:11px;color:#bbb;padding-left:14px;display:flex;align-items:center}
.newsletter .sub{width:111px;background:var(--blue);color:var(--white);font-size:11px;font-weight:700;display:flex;align-items:center;justify-content:center}
.info{position:absolute;top:3684px;font-size:12.5px;line-height:20px;color:var(--white)}
.divider{position:absolute;left:114px;top:3800px;width:972px;height:1px;background:#333}
.copy{top:3838px;font-size:14px;color:var(--white)}
</style>
</head>
<body>

<header class="site-header">
  <nav class="nav">
    <a style="left:427px">Home</a>
    <a style="left:523px">About Us</a>
    <a style="left:641px">Services</a>
    <a style="left:753px">Contact Us</a>
  </nav>
  <div class="login">
    <svg width="14" height="16" viewBox="0 0 14 16"><circle cx="7" cy="4" r="4" fill="#fff"/><path d="M0 16c0-5 3-7 7-7s7 2 7 7z" fill="#fff"/></svg>
    Login
  </div>
</header>
<div class="brand"><span>KRV</span><small>MAINTENANCE</small></div>

<section class="hero" role="img" aria-label="Oil pumpjacks silhouetted against a sunset sky reflected in still water"></section>
<div class="abs center hero-welcome">WELCOME TO</div>
<div class="abs center hero-big">KRV</div>
<div class="abs center hero-sub">MAINTENANCE</div>
<div class="abs center hero-text">Lorem ipsum dolor sit amet, consectetur adipiscing elit,<br>sed do eiusmod tempor incididunt ut</div>
<div class="btn btn-blue" style="left:523px;top:570px;width:154px;height:48px;font-size:15px">GET STARTED</div>

<h2 class="abs center section-title" style="top:838px">OUR SERVICES</h2>
<p class="services-text">Lorem ipsum dolor sit amet, consectetur adipiscing elit, sed do eiusmod tempor incididunt ut labore et dolore magna aliqua. Quis ipsum suspendisse ultrices gravida. Risus commodo viverra maecenas accumsan lacus vel facilisis. Lorem ipsum dolor sit amet, consectetur adipiscing elit, sed do eiusmod tempor incididunt ut labore et dolore magna aliqua. Quis ipsum suspendisse ultrices gravida. Risus commodo viverra maecenas accumsan lacus vel facilisis.</p>
<div class="btn btn-blue" style="left:532px;top:1033px;width:136px;height:49px;font-size:16px">Read More</div>

<div class="service-card" style="left:155px;top:1055px;height:325px">
  <div class="photo" role="img" aria-label="Drill rig pumpjack on a hillside" style="background:linear-gradient(180deg,#d8dcdf 0%,#8b9598 45%,#5a5f4e 75%,#3e3a30 100%)"><div class="label">Drill Rigs</div></div>
</div>
<div class="service-card" style="left:468px;top:1132px;height:323px">
  <div class="photo" role="img" aria-label="Close-up of a large boat engine" style="background:linear-gradient(160deg,#8e949a 0%,#5e656c 45%,#3a3f45 100%)"><div class="label">Large boats</div></div>
</div>
<div class="service-card" style="left:803px;top:1064px;height:324px">
  <div class="photo" role="img" aria-label="Excavator on a site at sunset" style="background:linear-gradient(180deg,#c98a48 0%,#8a5a30 40%,#3b2e24 75%,#231a14 100%)"><div class="label">Earthmoving<br>Equipment</div></div>
</div>

<div class="about-band"></div>
<div class="about-photo" role="img" aria-label="Technician in a hard hat working on industrial valves and pipes"></div>
<h2 class="about-title">WHERE WE COME FROM</h2>
<p class="about-text">Director of the company has over 20-year experience in the fixed and mobile plant industries ranging from Perth local and overseas. Facilities like precious metals refining, offshore drilling and production platform, open cut and underground mining, civils, geotechnical and construction equipment and large-scale construction as an expat overseas. We offer personalised service to all small and medium size business across a diverse range of industries.</p>
<div class="btn btn-white" style="left:595px;top:1942px;width:152px;height:50px;font-size:16px">Read More</div>

<h2 class="abs center section-title" style="top:2183px;font-size:36px">CLIENT'S TESTIMONIAL</h2>
<div class="t-photo" style="left:98px" role="img" aria-label="Portrait of a smiling male client"></div>
<div class="t-card" style="left:280px">
  <h3>Marlon Teague</h3><div class="role">Lorem Ipsum</div><div class="rule"></div>
  <div class="stars">★★★☆☆</div>
  <p>Lorem ipsum dolor sit amet, consectetur adipiscing elit, sed do eiusmod tempor incididunt ut labore et dolore magna aliqua. Quis ipsum</p>
</div>
<div class="t-photo" style="left:614px;background:linear-gradient(160deg,#eaeaea,#a8735a 55%,#d43a3a)" role="img" aria-label="Portrait of a smiling female client"></div>
<div class="t-card" style="left:795px">
  <h3>Elise Varga</h3><div class="role">Lorem Ipsum</div><div class="rule"></div>
  <div class="stars">★★★☆☆</div>
  <p>Lorem ipsum dolor sit amet, consectetur adipiscing elit, sed do eiusmod tempor incididunt ut labore et dolore magna aliqua. Quis ipsum</p>
</div>

<div class="footer-bg"></div>
<div class="contact-card"></div>
<h2 class="abs center section-title" style="top:2885px;font-size:40px">CONTACT US</h2>
<p class="contact-text">Lorem ipsum dolor sit amet, consectetur adipiscing elit, sed do eiusmod tempor incididunt ut labore et dolore magna aliqua. Quis ipsum suspendisse ultrices gravida.ilisis.</p>
<div class="field" style="left:135px;top:3039px;width:453px;height:50px">Name
  <svg width="12" height="13" viewBox="0 0 14 16"><circle cx="7" cy="4" r="4" fill="#666"/><path d="M0 16c0-5 3-7 7-7s7 2 7 7z" fill="#666"/></svg></div>
<div class="field" style="left:600px;top:3039px;width:460px;height:50px">Email
  <svg width="14" height="11" viewBox="0 0 14 11"><rect width="14" height="11" rx="1" fill="#666"/><path d="M0 1l7 5 7-5" stroke="#f1f1f1" stroke-width="1.5" fill="none"/></svg></div>
<div class="field area" style="left:135px;top:3115px;width:928px;height:132px">Message</div>
<div class="btn btn-blue" style="left:504px;top:3280px;width:190px;height:50px;font-size:13px;font-weight:700">SEND MESSAGE</div>

<div class="foot-brand"><span>KRV</span><small>MAINTENANCE</small></div>
<div class="foot-h" style="left:515px;top:3515px;font-size:24px">OUR NEWSLETTER</div>
<div class="newsletter"><div class="input">Email Address</div><div class="sub">SUBSCRIBE</div></div>
<div class="foot-h" style="left:515px;top:3642px;font-size:15px">CONTACT US</div>
<svg class="abs" style="left:516px;top:3688px" width="11" height="15" viewBox="0 0 12 16"><path d="M6 0a6 6 0 0 0-6 6c0 4.5 6 10 6 10s6-5.5 6-10a6 6 0 0 0-6-6z" fill="#1a73d9"/><circle cx="6" cy="6" r="2.3" fill="#000"/></svg>
<div class="info" style="left:537px">14 KRV Works<br>&amp; Sales,LLC Lorem ipsum<br>dolor sit amet</div>
<svg class="abs" style="left:746px;top:3690px" width="15" height="15" viewBox="0 0 24 24"><path d="M6.6 10.8a15 15 0 0 0 6.6 6.6l2.2-2.2c.3-.3.7-.4 1-.2 1.1.4 2.3.6 3.6.6.6 0 1 .4 1 1V20c0 .6-.4 1-1 1A17 17 0 0 1 3 4c0-.6.4-1 1-1h3.5c.6 0 1 .4 1 1 0 1.3.2 2.5.6 3.6.1.3 0 .7-.2 1z" fill="#1a73d9"/></svg>
<div class="info" style="left:770px">Phone<br>555-014-2297</div>
<svg class="abs" style="left:888px;top:3690px" width="16" height="15" viewBox="0 0 16 14"><path d="M1 5l7-4 7 4v8H1z" fill="none" stroke="#1a73d9" stroke-width="1.5"/><path d="M1 5l7 4 7-4" fill="none" stroke="#1a73d9" stroke-width="1.5"/></svg>
<div class="info" style="left:912px">Email<br>hello@krvmaintenance.com</div>
<div class="divider"></div>
<div class="abs center copy">© 2023 KRV Maintenance Services Pty Ltd. All rights reserved. Terms And Conditions</div>

</body>
</html>
```